THE WELLNESS BARN WEBSITE for Physio, Fitness, health

An attractive website advertising a physiotherapyand fitness / gym business, not generic, colours are natural, greens, browns, beiges. No cheesy pictures. With the ability to sell a small,amount of goods online if i decide to. Simple to navigate. Text boxes that i can input the main information and change easily. Somewhere to put my timetable. Easy to find contact details. However many pages it needs, im not fussed.
Target Market(s)
People looking for rehabilitation or fitness classes
Industry/Entity Type
Physiotherapy, Fitness, Gym, Health
Coding
Coded - Design and coding required
Number of Pages Required
1 page
Font styles to use
Other font styles liked:
- Im not fusse,ld, not script
Requirements
Must have
- Will upload posts from my business insta page for reference about the feel. Earthy natural tones, I have a lot of timber, and rustic looking piece's, plants etc in my clinic
Nice to have
- Simple to navigate
Should not have
- Cheesy "yoga" or generic "people doing physio" pics

```html
<!DOCTYPE html>
<html lang="en">
<head>
<meta charset="utf-8">
<title>The Wellness Barn – Rehabilitation &amp; Fitness</title>
<link href="https://fonts.googleapis.com/css2?family=Oswald:wght@500;600;700&family=Roboto:wght@400;500;700&family=Great+Vibes&display=swap" rel="stylesheet">
<style>
:root{
  --green:#2f4a1f;
  --green-mid:#3d5a26;
  --brown:#6b3a0e;
  --brown-dark:#4a2a0c;
  --beige:#f2efe8;
  --beige-2:#e9e4d6;
  --sand:#ebe6d3;
  --wood:#3b2515;
  --wood-light:#5a3a22;
  --text:#2b2b2b;
  --muted:#555;
  --white:#fff;
}
*{box-sizing:border-box;margin:0;padding:0}
html,body{width:1200px;height:4878px;overflow:hidden}
body{position:relative;background:var(--beige);font-family:"Roboto",Arial,sans-serif;color:var(--text)}
.abs{position:absolute}
.heading{font-family:"Oswald",Impact,sans-serif;font-weight:600;text-transform:uppercase;color:var(--green);font-size:32px;letter-spacing:.5px}
.script{font-family:"Great Vibes",cursive;color:var(--green);opacity:.22;font-size:44px;position:absolute;white-space:nowrap}
.btn{position:absolute;display:flex;align-items:center;justify-content:center;font-size:13px;color:var(--white);text-decoration:none;border-radius:3px}
.btn-green{background:var(--green)}
.btn-brown{background:var(--brown)}
.photo{position:absolute;border-radius:10px}
.log{z-index:0}
.brand{font-family:"Oswald",Impact,sans-serif;font-weight:700;color:var(--green);text-transform:uppercase;line-height:1;display:flex;align-items:center;gap:8px}

/* header */
.hero{left:0;top:0;width:1200px;height:583px;overflow:hidden}
.hero-photo{left:0;top:0;width:1200px;height:583px;background:linear-gradient(90deg,#f4f2ea 0%,#f0eee4 35%,#d8e2d6 58%,#c3d3cb 75%,#a9bfb3 100%)}
.hero-blob{left:0;top:0}
.topbar{right:142px;top:10px;display:flex;gap:28px;font-size:13px;color:var(--text)}
.topbar span{display:flex;align-items:center;gap:6px}
.nav{left:592px;top:42px;width:608px;height:34px;background:var(--brown);border-radius:17px 0 0 17px;display:flex;align-items:center;padding-left:18px}
.nav a{color:var(--white);text-decoration:none;font-size:12px;padding:7px 14px;text-transform:uppercase}
.nav a.active{background:var(--brown-dark);border-radius:14px;font-weight:700}
.hero-title{left:142px;top:222px;font-family:"Oswald",Impact,sans-serif;font-weight:700;font-size:40px;line-height:49px;text-transform:uppercase;color:var(--green)}
.hero-title .accent{color:var(--brown)}

/* about */
.about-text{left:647px;top:778px;width:410px}
.about-text p{font-size:12.5px;line-height:23px;color:var(--muted);margin-top:14px}

/* wood bands */
.wood{left:0;width:1200px;background:linear-gradient(180deg,rgba(59,37,21,0) 0%,var(--wood) 14%,var(--wood-light) 50%,var(--wood) 86%,rgba(59,37,21,0) 100%)}
.wood .heading{color:var(--white)}
.wood .script{color:var(--white);opacity:.18}

/* services */
.service{position:absolute;top:1405px;width:211px;height:280px;background:rgba(20,12,6,.82);border-radius:8px;padding:24px 16px;color:var(--white)}
.service.featured{background:var(--green-mid)}
.service .icon{width:82px;height:82px;border-radius:50%;background:var(--white);display:flex;align-items:center;justify-content:center}
.service h3{font-size:15px;font-weight:500;text-transform:uppercase;margin-top:40px}
.service p{font-size:12px;line-height:24px;margin-top:6px;color:#e8e2d8}
.service .more{font-size:12px;margin-top:12px;display:block}

/* timetable */
.center-text{position:absolute;left:0;width:1200px;text-align:center}
.lead{font-size:12.5px;line-height:22px;color:var(--muted)}
.timetable{position:absolute;z-index:2;left:142px;top:2092px;width:918px;border-collapse:collapse;font-size:12px;background:var(--sand);box-shadow:0 6px 14px rgba(0,0,0,.12)}
.timetable th{background:#8c9a7a;color:var(--white);font-weight:400;height:37px}
.timetable th.today{background:var(--green)}
.timetable td{height:34.6px;border:1px solid #d4ccb2;text-align:center;color:#333}
.timetable td.time{width:106px}
.timetable td.now{background:var(--green);color:var(--white)}
.timetable td.hl{background:var(--green-mid);color:var(--white)}

/* why */
.feature{position:absolute;width:250px;font-size:12.5px;line-height:23px;color:var(--muted)}
.feature h4{font-size:14.5px;font-weight:500;text-transform:uppercase;color:var(--green);margin:8px 0 6px}
.feature .ring{width:80px;height:80px;border-radius:50%;background:#e4d8c3;display:flex;align-items:center;justify-content:center}

/* testimonials */
.quote{position:absolute;width:283px;background:var(--white);border-radius:6px;padding:22px 20px;font-size:12.5px;line-height:23px;text-align:center;color:#333}
.quote.featured{background:var(--green-mid);color:var(--white)}
.quote .who{display:flex;align-items:center;gap:10px;margin-top:14px;text-align:left;font-size:13px}
.quote .avatar{width:60px;height:60px;border-radius:50%;background:linear-gradient(135deg,#c9b8a6,#8a7565);border:3px solid #fff;flex:none}
.quote .who small{display:block;font-size:11px;opacity:.85}
.quote .stars{margin-left:auto;color:#f2a514;letter-spacing:1px}
.arrow-btn{position:absolute;width:36px;height:36px;border-radius:50%;display:flex;align-items:center;justify-content:center}

/* footer */
.foot-col{position:absolute;top:4550px;font-size:12.5px;color:#333}
.foot-col h5{font-size:14px;font-weight:500;text-transform:uppercase;margin-bottom:18px}
.foot-col li{list-style:none;margin-bottom:13px}
.foot-col li::before{content:"» ";}
.contact-row{display:flex;gap:10px;margin-bottom:14px;line-height:19px}
.bottom-bar{left:0;top:4793px;width:1200px;height:85px;background:var(--brown);color:var(--white);font-size:12px}
.social{position:absolute;width:26px;height:26px;border-radius:50%;background:var(--white)}
</style>
</head>
<body>

<!-- HERO -->
<section class="abs hero">
  <div class="abs hero-photo" role="img" aria-label="Soft-lit treatment room with a massage table, sheer curtains and a plant"></div>
  <svg class="abs hero-blob" width="560" height="260" viewBox="0 0 560 260"><path d="M0 0H560C520 60 430 90 330 110C220 130 150 150 90 200C50 232 20 250 0 255Z" fill="#8e9f7e" opacity=".55"/><path d="M0 0H420C380 50 300 70 220 90C130 110 60 150 0 190Z" fill="#6c7f5c" opacity=".55"/></svg>
  <div class="abs brand" style="left:142px;top:28px;font-size:26px;width:140px;flex-wrap:wrap;line-height:1.05">The Wellness Barn</div>
  <div class="abs topbar">
    <span><svg width="14" height="14" viewBox="0 0 24 24"><path d="M6.6 10.8a15 15 0 006.6 6.6l2.2-2.2c.3-.3.7-.4 1-.2 1.1.4 2.3.6 3.6.6.6 0 1 .4 1 1V20c0 .6-.4 1-1 1A17 17 0 013 4c0-.6.4-1 1-1h3.5c.6 0 1 .4 1 1 0 1.3.2 2.5.6 3.6.1.3 0 .7-.2 1z" fill="#2b2b2b"/></svg>123 555 0199</span>
    <span><svg width="15" height="12" viewBox="0 0 24 18"><rect x="1" y="1" width="22" height="16" fill="none" stroke="#2b2b2b" stroke-width="2"/><path d="M1 1l11 9 11-9" fill="none" stroke="#2b2b2b" stroke-width="2"/></svg>info@thewellnessbarn.com.au</span>
  </div>
  <nav class="abs nav">
    <a class="active" href="#">Home</a><a href="#">Services</a><a href="#">About Us</a><a href="#">Timetable</a><a href="#">Contact Us</a>
  </nav>
  <h1 class="abs hero-title">Welcome to the Wellness<br>Barn-your space for<br><span class="accent">rehabilitation &amp; fitness.</span></h1>
  <a class="btn btn-green" href="#" style="left:142px;top:386px;width:140px;height:34px">Book Your Session</a>
</section>

<!-- ABOUT -->
<section>
  <div class="photo" style="left:142px;top:674px;width:210px;height:282px;background:linear-gradient(160deg,#8c7458,#3e3126)" role="img" aria-label="Gym interior with timber walls and hanging rings"></div>
  <div class="photo" style="left:355px;top:686px;width:100px;height:100px;border-radius:50%;background:radial-gradient(circle,#e3b77a,#b9803f 70%,#7a4a1e)" role="img" aria-label="Timber log slice"></div>
  <div class="photo" style="left:240px;top:970px;width:170px;height:160px;border-radius:50%;background:radial-gradient(circle,#4f8a34,#2b5a1c 70%,rgba(43,90,28,0))" role="img" aria-label="Tropical green plant leaves"></div>
  <div class="photo" style="left:365px;top:780px;width:210px;height:280px;background:linear-gradient(160deg,#9a9a9a,#2c2c2c)" role="img" aria-label="Client training on a rowing machine, seen from behind"></div>
  <div class="about-text abs">
    <div class="script" style="left:0;top:-18px">Who We Are</div>
    <h2 class="heading">About The Wellness Barn</h2>
    <p>Lorem ipsum dolor sit amet, consectetuer adipiscing elit, sed diam nonummy nibh euismod tincidunt ut laoreet dolore magna aliquam erat volutpat. Ut wisi enim ad minim veniam, quis nostrud exerci tation ullamcorper suscipit lobortis nisl ut aliquip ex ea commodo consequat. Duis autem vel eum iriure dolor in hendrerit in vulputate velit esse molestie consequat, vel illum dolore eu feugiat nulla facilisis at vero eros et accumsan et iusto odio dignissim qui blandit praesent luptatum zzril delenit augue duis dolore te feugait nulla facilisi.</p>
  </div>
  <a class="btn btn-brown" href="#" style="left:647px;top:1026px;width:107px;height:34px">Read More</a>
</section>

<!-- SERVICES -->
<section class="abs wood" style="top:1210px;height:700px">
  <div class="script" style="left:478px;top:88px">What We Do</div>
  <h2 class="heading center-text" style="top:120px">Our Services</h2>
</section>
<div class="service" style="left:142px">
  <div class="icon"><svg width="46" height="46" viewBox="0 0 48 48" fill="none" stroke="#2f4a1f" stroke-width="2"><circle cx="16" cy="14" r="5"/><path d="M6 34h36M10 34v6M38 34v6M12 28h24l-4-6H18z"/></svg></div>
  <h3>Physiotherapy</h3><p>Expert care for injury recovery and pain management.</p><span class="more">Read More »</span>
</div>
<div class="service featured" style="left:377px">
  <div class="icon"><svg width="46" height="46" viewBox="0 0 48 48" fill="none" stroke="#2f4a1f" stroke-width="2"><circle cx="22" cy="10" r="5"/><path d="M22 15v14l-8 12M22 29l8 12M12 22h20M34 18v20"/></svg></div>
  <h3>Rehabilitation</h3><p>Expert care for injury recovery and pain management.</p><span class="more">Read More »</span>
</div>
<div class="service" style="left:611px">
  <div class="icon"><svg width="46" height="46" viewBox="0 0 48 48" fill="none" stroke="#2f4a1f" stroke-width="2"><circle cx="24" cy="10" r="5"/><path d="M24 15v12M14 20l10 4 10-4M16 40l8-13 8 13"/><circle cx="24" cy="27" r="16"/></svg></div>
  <h3>Fitness Classes</h3><p>Expert care for injury recovery and pain management.</p><span class="more">Read More »</span>
</div>
<div class="service" style="left:846px">
  <div class="icon"><svg width="46" height="46" viewBox="0 0 48 48" fill="none" stroke="#2f4a1f" stroke-width="2"><circle cx="16" cy="10" r="5"/><path d="M16 15v16l-6 10M16 31l6 10M8 22h16M30 8h12v14H30zM36 22v18"/></svg></div>
  <h3>Personal Training</h3><p>Expert care for injury recovery and pain management.</p><span class="more">Read More »</span>
</div>
<a class="btn" href="#" style="left:547px;top:1723px;width:106px;height:34px;background:#fff;color:#333">View All</a>

<!-- TIMETABLE -->
<div class="script" style="left:540px;top:1940px">Schedule</div>
<h2 class="heading center-text" style="top:1966px">My Timetable</h2>
<p class="center-text lead" style="top:2016px">Lorem ipsum dolor sit amet, consectetuer adipiscing elit, sed diam nonummy nibh<br>euismod tincidunt ut laoreet dolore magna aliquam erat volutpat.</p>
<div class="photo log" style="left:1000px;top:2040px;width:105px;height:105px;border-radius:50%;background:radial-gradient(circle,#e6bd82,#b57c3c 70%,#7a4a1e)" role="img" aria-label="Timber log slice"></div>
<div class="photo log" style="left:60px;top:2275px;width:130px;height:165px;border-radius:50%;background:radial-gradient(circle,#4d7f33,#a56f35 62%,#7a4a1e 75%,rgba(122,74,30,0) 80%)" role="img" aria-label="Log slice with green plant"></div>
<table class="timetable">
  <tr><th>Time</th><th>Monday</th><th class="today">Tuesday</th><th>Wednesday</th><th>Thursday</th><th>Friday</th><th>Saturday</th><th>Sunday</th></tr>
  <tr><td class="time">07:00-08:30</td><td>Yoga Class</td><td></td><td>Fitness Class</td><td></td><td></td><td>Yoga Class</td><td></td></tr>
  <tr><td class="time">08:30-09:45</td><td>Physiotherapy</td><td></td><td></td><td></td><td></td><td></td><td>Physiotherapy</td></tr>
  <tr><td class="time">09:45-10:30</td><td></td><td></td><td>Yoga Class</td><td></td><td>Strength Training</td><td></td><td></td></tr>
  <tr><td class="time now">10:30-11:30</td><td></td><td class="hl">Strength Training</td><td></td><td>Physiotherapy</td><td></td><td></td><td></td></tr>
  <tr><td class="time">11:30-13:00</td><td></td><td></td><td>Fitness</td><td></td><td></td><td></td><td></td></tr>
  <tr><td class="time">14:00-14:30</td><td></td><td>Yoga Class</td><td></td><td></td><td></td><td></td><td>Strength Training</td></tr>
  <tr><td class="time">16:00-17:00</td><td>Yoga Class</td><td></td><td></td><td>Fitness Class</td><td></td><td>Physiotherapy</td><td></td></tr>
</table>
<a class="btn btn-green" href="#" style="left:538px;top:2408px;width:106px;height:34px">Book Now</a>

<!-- WHY CHOOSE US -->
<div class="script" style="left:520px;top:2532px">Difference</div>
<h2 class="heading center-text" style="top:2558px">Why Choose Us?</h2>
<p class="center-text lead" style="top:2608px">Lorem ipsum dolor sit amet, consectetuer adipiscing elit, sed diam<br>nonummy nibh euismod tincidunt ut laoreet dolore magna aliquam erat.</p>
<div class="abs brand" style="left:462px;top:2700px;width:280px;font-size:58px;flex-direction:column;text-align:center;gap:0">The<br>Wellness<br>Barn</div>
<div class="feature" style="left:142px;top:2686px;text-align:right">
  <div class="ring" style="margin-left:auto;margin-right:28px"><svg width="44" height="44" viewBox="0 0 48 48" fill="none" stroke="#8a5a2b" stroke-width="2"><circle cx="16" cy="14" r="5"/><circle cx="32" cy="14" r="5"/><path d="M8 40V26c0-3 3-5 8-5s8 2 8 5v14M24 40V26c0-3 3-5 8-5s8 2 8 5v14"/></svg></div>
  <h4>Experienced Staff</h4>Loreet dolore magna aliquam erat volutpat. Ut wisi enim ad minim veniam, quis nostrud agna aliquam exerci tation.
</div>
<div class="feature" style="left:802px;top:2686px">
  <div class="ring" style="margin-left:2px"><svg width="44" height="44" viewBox="0 0 48 48" fill="none" stroke="#8a5a2b" stroke-width="2"><path d="M24 40V22M24 22c0-8 6-12 12-12 0 8-6 12-12 12zM24 26c0-6-5-10-11-10 0 6 5 10 11 10zM14 40h20"/></svg></div>
  <h4>Natural Environment</h4>Loreet dolore magna aliquam erat volutpat. Ut wisi enim ad minim veniam, quis nostrud agna aliquam exerci tation.
</div>
<div class="feature" style="left:470px;top:2942px;text-align:center">
  <div class="ring" style="margin:0 auto"><svg width="44" height="44" viewBox="0 0 48 48" fill="none" stroke="#8a5a2b" stroke-width="2"><circle cx="20" cy="20" r="12"/><circle cx="20" cy="20" r="6"/><rect x="24" y="26" width="16" height="14" rx="2"/><path d="M28 31h8M28 35h8"/></svg></div>
  <h4>Personalized Plans</h4>Loreet dolore magna aliquam erat volutpat. Ut wisi enim ad minim veniam, quis nostrud agna aliquam exerci tation.
</div>

<!-- TESTIMONIALS -->
<section class="abs wood" style="top:3200px;height:690px">
  <div class="script" style="left:500px;top:130px">Testimonials</div>
  <h2 class="heading center-text" style="top:155px">Happy Client Sayings</h2>
</section>
<div class="arrow-btn" style="left:90px;top:3512px;background:#8a8a80"><svg width="14" height="14" viewBox="0 0 24 24"><path d="M15 5l-7 7 7 7" fill="none" stroke="#fff" stroke-width="3"/></svg></div>
<div class="arrow-btn" style="left:1072px;top:3512px;background:#fff"><svg width="14" height="14" viewBox="0 0 24 24"><path d="M9 5l7 7-7 7" fill="none" stroke="#333" stroke-width="3"/></svg></div>
<div class="quote" style="left:142px;top:3455px">Lorem ipsum dolor sit amet, consectetuer adipiscing elit, sed diam nonu mmy nibh euismod tincidunt ut laoreet dolore magna aliquam erat volut pat. Ut wisi enim ad minim veniam, quis nostrud exerci.
  <div class="who"><div class="avatar" role="img" aria-label="Client portrait"></div><div><b>Jordan P.</b><small>Lorem ipsum</small></div><span class="stars">★★★★★</span></div>
</div>
<div class="quote featured" style="left:458px;top:3417px">Lorem ipsum dolor sit amet, consectetuer adipiscing elit, sed diam nonu mmy nibh euismod tincidunt ut laoreet dolore magna aliquam erat volut pat. Ut wisi enim ad minim veniam, quis nostrud exerci.
  <div class="who"><div class="avatar" role="img" aria-label="Client portrait"></div><div><b>Ellen Hart</b><small>Lorem ipsum</small></div><span class="stars">★★★★★</span></div>
</div>
<div class="quote" style="left:776px;top:3455px">Lorem ipsum dolor sit amet, consectetuer adipiscing elit, sed diam nonu mmy nibh euismod tincidunt ut laoreet dolore magna aliquam erat volut pat. Ut wisi enim ad minim veniam, quis nostrud exerci.
  <div class="who"><div class="avatar" role="img" aria-label="Client portrait"></div><div><b>Sofia Lane</b><small>Lorem ipsum</small></div><span class="stars">★★★★★</span></div>
</div>

<!-- GALLERY -->
<div class="script" style="left:530px;top:3928px">Showcase</div>
<h2 class="heading center-text" style="top:3954px">Photo Gallery</h2>
<div class="photo" style="left:142px;top:4028px;width:252px;height:171px;background:linear-gradient(135deg,#7fa04a,#2f5a22)" role="img" aria-label="Spray bottle product among green leaves"></div>
<div class="photo" style="left:142px;top:4214px;width:252px;height:166px;background:linear-gradient(135deg,#8a7a68,#b86a3f)" role="img" aria-label="Wheat bag heat pack with gift box"></div>
<div class="photo" style="left:405px;top:4028px;width:388px;height:352px;background:linear-gradient(135deg,#b8b2a6,#6f6a5e 55%,#3f4a30)" role="img" aria-label="Branded cap and t-shirt merchandise"></div>
<div class="photo" style="left:806px;top:4013px;width:254px;height:193px;background:linear-gradient(135deg,#a68a6a,#6b4a3a)" role="img" aria-label="Branded drink coolers among dried leaves"></div>
<div class="photo" style="left:806px;top:4218px;width:254px;height:162px;background:linear-gradient(135deg,#7a6a58,#c8c0b0)" role="img" aria-label="Gift box with wellness products"></div>

<!-- FOOTER -->
<div class="abs" style="left:142px;top:4468px;width:918px;height:1px;background:#9a9a88"></div>
<div class="abs brand" style="left:142px;top:4560px;width:200px;font-size:40px;flex-direction:column;align-items:flex-start;gap:0">The<br>Wellness<br>Barn</div>
<div class="foot-col" style="left:405px">
  <h5>Quick Links</h5>
  <ul><li>Home</li><li>Services</li><li>About Us</li><li>Timetable</li><li>Contact Us</li></ul>
</div>
<div class="foot-col" style="left:598px;width:230px">
  <h5>Contact Details</h5>
  <div class="contact-row"><svg width="14" height="18" viewBox="0 0 24 30"><path d="M12 1a10 10 0 00-10 10c0 8 10 18 10 18s10-10 10-18A10 10 0 0012 1zm0 14a4 4 0 110-8 4 4 0 010 8z" fill="#2b2b2b"/></svg><span>12/48 Ridge Creek Road,<br>Millbrook, QLD 4600</span></div>
  <div class="contact-row"><svg width="14" height="14" viewBox="0 0 24 24"><path d="M6.6 10.8a15 15 0 006.6 6.6l2.2-2.2c.3-.3.7-.4 1-.2 1.1.4 2.3.6 3.6.6.6 0 1 .4 1 1V20c0 .6-.4 1-1 1A17 17 0 013 4c0-.6.4-1 1-1h3.5c.6 0 1 .4 1 1 0 1.3.2 2.5.6 3.6.1.3 0 .7-.2 1z" fill="#2b2b2b"/></svg><span>Phone<br>123 555 0199</span></div>
  <div class="contact-row"><svg width="14" height="11" viewBox="0 0 24 18"><rect x="1" y="1" width="22" height="16" fill="none" stroke="#2b2b2b" stroke-width="2"/><path d="M1 1l11 9 11-9" fill="none" stroke="#2b2b2b" stroke-width="2"/></svg><span>Email<br>info@thewellnessbarn.com.au</span></div>
</div>
<div class="foot-col" style="left:858px">
  <h5>Locations</h5>
  <div style="width:202px;height:132px;border-radius:6px;background:linear-gradient(135deg,#e8eef0,#d6e2d4)" role="img" aria-label="Location map"></div>
</div>
<svg class="abs" style="left:860px;top:4640px" width="340" height="160" viewBox="0 0 340 160"><path d="M40 160C70 100 150 60 250 50C300 45 330 20 340 0V160Z" fill="#8e9f7e" opacity=".6"/><path d="M140 160C170 120 240 100 340 80V160Z" fill="#6c7f5c" opacity=".7"/></svg>
<footer class="abs bottom-bar">
  <div class="abs" style="left:122px;top:34px">© 2025 THE WELLNESS BARN. All Rights Reserved.</div>
  <span class="social" style="left:960px;top:28px"></span>
  <span class="social" style="left:996px;top:28px"></span>
  <span class="social" style="left:1032px;top:28px"></span>
</footer>

</body>
</html>
```